Business Card Design for Occupational Medicine Start Up Company

We need to design a professional business card. We are a healthcare company providing occupational medicine services to blue collar industries. We are professional, efficient and high quality service providers.

Target Market(s)

Blue Collar Industry: Shipbuilding, Ports, Trucking Companies; The Executives and Safety Officers for these companies

Industry/Entity Type

Healthcare

Contact Information for Business Card

Logo, Name, Title, Email, Phone

Other font styles liked:
• Please match our Brand Guide

Requirements
Must have
• Our Company Colors and Logo

```html
<!DOCTYPE html>
<html lang="en">
<head>
<meta charset="utf-8">
<title>Shiftline Clinics – Business Card</title>
<link href="https://fonts.googleapis.com/css2?family=Montserrat:wght@400;500;600&display=swap" rel="stylesheet">
<style>
  :root {
    --backdrop: #2a2a2a;
    --navy: #332f78;
    --sky: #2e9ad6;
    --amber: #eeab3d;
    --paper: #f4f4f2;
    --white: #ffffff;
  }
  * { margin: 0; padding: 0; box-sizing: border-box; }
  html, body {
    width: 1200px; height: 1200px; overflow: hidden;
    background: var(--backdrop);
    font-family: "Montserrat", Arial, sans-serif;
  }
  .stage { position: relative; width: 1200px; height: 1200px; }
  .card {
    position: absolute;
    width: 594px; height: 348px;
    border-radius: 21px;
    overflow: hidden;
  }
  .card-front { left: 298px; top: 200px; background: var(--navy); }
  .card-back { left: 292px; top: 637px; background: var(--paper); }

  .brand-name {
    position: absolute;
    color: var(--white);
    font-weight: 600;
    text-align: center;
    line-height: 1.05;
    letter-spacing: 0.5px;
  }
  .brand-name .sub { display: block; font-size: 0.6em; letter-spacing: 0.35em; margin-top: 2px; }
  .card-front .brand-name { left: 29px; top: 255px; font-size: 29px; }
  .card-front .brand-dot {
    position: absolute; left: 312px; top: 34px;
    width: 240px; height: 240px; border-radius: 50%;
    background: var(--sky);
  }

  .back-shape { position: absolute; inset: 0; }
  .card-back .brand-dot {
    position: absolute; left: 126px; top: 96px;
    width: 56px; height: 56px; border-radius: 50%;
    background: var(--sky);
  }
  .card-back .brand-name { left: 0; width: 300px; top: 177px; font-size: 26px; }

  .contact {
    position: absolute; right: 30px; top: 44px;
    text-align: right; color: var(--navy);
  }
  .contact .person { font-size: 23px; font-weight: 600; color: var(--sky); letter-spacing: 0.5px; line-height: 1.1; }
  .contact .role { font-size: 15px; font-weight: 500; margin-top: 2px; }
  .details {
    position: absolute; right: 30px; top: 205px;
    text-align: right; color: var(--navy);
    font-size: 15px; font-weight: 500; line-height: 21px;
  }
  .details .address { margin-right: 0; }
  .details ul { list-style: none; margin-top: 5px; }
  .details li { display: flex; justify-content: flex-end; align-items: center; gap: 12px; }
  .details svg { width: 13px; height: 13px; flex: none; }
</style>
</head>
<body>
<main class="stage">

  <section class="card card-front" aria-label="Card front">
    <div class="brand-dot" aria-hidden="true"></div>
    <p class="brand-name">SHIFTLINE<span class="sub">CLINICS</span></p>
  </section>

  <section class="card card-back" aria-label="Card back">
    <svg class="back-shape" viewBox="0 0 594 348" aria-hidden="true">
      <path d="M258 0 Q330 174 249 348" fill="none" stroke="var(--amber)" stroke-width="8"/>
      <path d="M0 0 H242 Q320 174 233 348 H0 Z" fill="var(--navy)"/>
    </svg>
    <div class="brand-dot" aria-hidden="true"></div>
    <p class="brand-name">SHIFTLINE<span class="sub">CLINICS</span></p>

    <div class="contact">
      <p class="person">DANA REYES</p>
      <p class="role">Senior Doctor</p>
    </div>

    <div class="details">
      <p class="address">48 Harbor Street, Suite 210<br>Bayview, State 54321</p>
      <ul>
        <li>555-014-2270
          <svg viewBox="0 0 16 16" aria-hidden="true"><path d="M3 2h3l1.5 4-2 1.2a9 9 0 0 0 3.3 3.3L10 8.5l4 1.5v3a1.5 1.5 0 0 1-1.5 1.5A11.5 11.5 0 0 1 1.5 3.5 1.5 1.5 0 0 1 3 2z" fill="var(--sky)"/></svg>
        </li>
        <li>hello@shiftline.com
          <svg viewBox="0 0 16 16" aria-hidden="true"><rect x="1" y="3" width="14" height="10" fill="var(--navy)"/><path d="M1 3l7 5 7-5" fill="none" stroke="var(--paper)" stroke-width="1.2"/></svg>
        </li>
        <li>www.shiftline.com
          <svg viewBox="0 0 16 16" aria-hidden="true"><circle cx="8" cy="8" r="6.5" fill="var(--amber)"/><path d="M1.5 8h13M8 1.5c-3 3.5-3 9.5 0 13M8 1.5c3 3.5 3 9.5 0 13" fill="none" stroke="var(--paper)" stroke-width="0.9"/></svg>
        </li>
      </ul>
    </div>
  </section>

</main>
</body>
</html>
```